Redesign of business card for Cedar Ridge Mechanical

We are looking for a new design for our business cards for Cedar Ridge Mechanical. We are a plumbing & HVAC construction company, operating on the West Coast of Canada and USA. Logo attached.
Industry/Entity Type
Construction - Plumbing & HVAC
Contact Information for Business Card
Name, address, phone numbers, email, website address
Look and feel
Each slider illustrates characteristics of the customer's brand and the style your logo design should communicate.

```html
<!DOCTYPE html>
<html lang="en">
<head>
<meta charset="utf-8">
<title>Cedar Ridge Mechanical – Business Card</title>
<link rel="stylesheet" href="https://fonts.googleapis.com/css2?family=Bebas+Neue&family=Montserrat:wght@400;600&display=swap">
<style>
  :root {
    --backdrop: #d8d3cb;
    --card: #2a2a2a;
    --ink-light: #ffffff;
    --ink-soft: #e6e6e6;
    --gloss: #0c0c0c;
    --card-shadow: rgba(0, 0, 0, 0.35);
  }
  * { margin: 0; padding: 0; box-sizing: border-box; }
  html, body {
    width: 900px;
    height: 1200px;
    overflow: hidden;
    background: var(--backdrop);
  }
  .canvas {
    position: relative;
    width: 900px;
    height: 1200px;
  }
  .card {
    position: absolute;
    left: 78px;
    width: 744px;
    height: 442px;
    background: var(--card);
    border-radius: 26px;
    box-shadow: 0 10px 24px var(--card-shadow);
    overflow: hidden;
  }
  .card--front { top: 130px; }
  .card--back { top: 638px; }

  .company-header {
    position: absolute;
    left: 37px;
    top: 48px;
    font-family: "Bebas Neue", sans-serif;
    font-size: 40px;
    letter-spacing: 1.6px;
    color: var(--ink-light);
    line-height: 1;
  }
  .person-name {
    position: absolute;
    left: 33px;
    top: 152px;
    font-family: "Montserrat", sans-serif;
    font-weight: 600;
    font-size: 24px;
    color: var(--ink-light);
  }
  .person-title {
    position: absolute;
    left: 33px;
    top: 185px;
    font-family: "Montserrat", sans-serif;
    font-size: 15px;
    color: var(--ink-soft);
  }
  .address {
    position: absolute;
    left: 37px;
    top: 243px;
    font-family: "Montserrat", sans-serif;
    font-size: 16px;
    line-height: 20px;
    color: var(--ink-soft);
  }
  .contact-list {
    position: absolute;
    left: 35px;
    top: 323px;
    list-style: none;
    font-family: "Montserrat", sans-serif;
    font-size: 15.5px;
    color: var(--ink-soft);
  }
  .contact-list li {
    display: flex;
    align-items: center;
    height: 31px;
  }
  .contact-icon {
    width: 16px;
    height: 16px;
    margin-right: 9px;
    fill: var(--ink-light);
  }
  .brand-name {
    position: absolute;
    font-family: "Bebas Neue", sans-serif;
    color: var(--gloss);
    text-align: center;
    line-height: 0.95;
  }
  .brand-name--front {
    left: 330px;
    top: 150px;
    width: 390px;
    font-size: 76px;
    letter-spacing: 2px;
  }
  .brand-name--back {
    left: 0;
    top: 130px;
    width: 744px;
    font-size: 96px;
    letter-spacing: 3px;
  }
</style>
</head>
<body>
<main class="canvas">
  <section class="card card--front" aria-label="Card front">
    <h1 class="company-header">CEDAR RIDGE MECHANICAL</h1>
    <p class="person-name">Daniel Reyes</p>
    <p class="person-title">Managing Director</p>
    <p class="address">240 Harbor View Road<br>Fairview, OR 97024</p>
    <ul class="contact-list">
      <li>
        <svg class="contact-icon" viewBox="0 0 24 24" aria-hidden="true"><path d="M6.6 10.8a15.1 15.1 0 0 0 6.6 6.6l2.2-2.2a1 1 0 0 1 1-.25 11.4 11.4 0 0 0 3.6.57 1 1 0 0 1 1 1V20a1 1 0 0 1-1 1A17 17 0 0 1 3 4a1 1 0 0 1 1-1h3.5a1 1 0 0 1 1 1c0 1.25.2 2.45.57 3.57a1 1 0 0 1-.25 1z"/></svg>
        555.210.4478
      </li>
      <li>
        <svg class="contact-icon" viewBox="0 0 24 24" aria-hidden="true"><path d="M3 6h18v1.2l-9 5.6-9-5.6z"/><path d="M3 9.3l9 5.6 9-5.6V18H3z"/></svg>
        info@cedarridgemechanical.com
      </li>
      <li>
        <svg class="contact-icon" viewBox="0 0 24 24" aria-hidden="true"><circle cx="12" cy="12" r="9"/><path d="M12 3v18M3 12h18" stroke="#2a2a2a" stroke-width="1.6" fill="none"/></svg>
        www.cedarridgemechanical.com
      </li>
    </ul>
    <p class="brand-name brand-name--front">CEDAR RIDGE<br>MECHANICAL</p>
  </section>

  <section class="card card--back" aria-label="Card back">
    <p class="brand-name brand-name--back">CEDAR RIDGE<br>MECHANICAL</p>
  </section>
</main>
</body>
</html>
```